RWT Fittings Ltd Business Cards

We need a business card with our business logo. We provide window and door installations on high-rises in west coast British Colombia, Canada.

I would like my business information and details on one side of the card, and the other side the company name with logo

Target Market(s)

General Contractors

Industry/Entity Type

Construction

Contact Information for Business Card

one side i want my company name and logo in the dark theme logo that i provided

Requirements
Must have
• Marco Peltieri, 16045518293, RWTFittings@mailbox-demo.com, 1407-5194 Linden Row Burnaby BC, V5H 2K9, Owner & Manager

```html
<!DOCTYPE html>
<html lang="en">
<head>
<meta charset="utf-8">
<title>RWT Fittings Ltd Business Cards</title>
<link href="https://fonts.googleapis.com/css2?family=Poppins:wght@300;400;600&display=swap" rel="stylesheet">
<style>
  :root {
    --backdrop: #1b1b1b;
    --card-light: #ffffff;
    --card-dark: #262626;
    --brand-blue: #1ea6df;
    --text-grey: #4a4a4a;
    --logo-grey: #8c8c8c;
  }
  html, body {
    margin: 0;
    padding: 0;
    width: 1200px;
    height: 897px;
    overflow: hidden;
    background: var(--backdrop);
    font-family: "Poppins", sans-serif;
  }
  .canvas {
    position: relative;
    width: 1200px;
    height: 897px;
  }
  .card {
    position: absolute;
    left: 304px;
    width: 594px;
    height: 338px;
    border-radius: 22px;
    box-sizing: border-box;
    overflow: hidden;
  }
  .card-front {
    top: 92px;
    background: var(--card-light);
  }
  .card-front .glow {
    position: absolute;
    right: -40px;
    top: -60px;
    width: 380px;
    height: 380px;
    border-radius: 50%;
    background: radial-gradient(circle, #f3f3f3 0%, #ffffff 70%);
  }
  .brand-name {
    position: absolute;
    left: 36px;
    top: 34px;
    margin: 0;
    font-weight: 600;
    font-size: 30px;
    letter-spacing: 1px;
    color: var(--brand-blue);
  }
  .accent-bar {
    position: absolute;
    left: 0;
    top: 158px;
    width: 18px;
    height: 34px;
    background: var(--brand-blue);
  }
  .person-name {
    position: absolute;
    left: 36px;
    top: 152px;
    margin: 0;
    font-weight: 600;
    font-size: 24px;
    color: var(--brand-blue);
    letter-spacing: 0.3px;
  }
  .person-role {
    position: absolute;
    left: 36px;
    top: 182px;
    margin: 0;
    font-weight: 300;
    font-size: 14px;
    color: var(--text-grey);
  }
  .address {
    position: absolute;
    left: 36px;
    top: 208px;
    margin: 0;
    font-style: normal;
    font-weight: 300;
    font-size: 15px;
    line-height: 19px;
    color: var(--text-grey);
    width: 300px;
  }
  .contacts {
    position: absolute;
    left: 36px;
    top: 256px;
    margin: 0;
    padding: 0;
    list-style: none;
    font-weight: 300;
    font-size: 15px;
    line-height: 18px;
    color: var(--text-grey);
  }
  .contacts li {
    display: flex;
    align-items: center;
    gap: 5px;
  }
  .contacts svg {
    width: 11px;
    height: 11px;
    flex: none;
  }
  .card-back {
    top: 470px;
    background: linear-gradient(135deg, #1f1f1f 0%, #2a2a2a 55%, #333333 100%);
    display: flex;
    align-items: center;
    justify-content: center;
    gap: 16px;
  }
  .back-mark {
    width: 34px;
    height: 34px;
    background: #141414;
  }
  .back-name {
    margin: 0;
    font-weight: 600;
    font-size: 40px;
    letter-spacing: 1px;
    color: var(--logo-grey);
  }
</style>
</head>
<body>
<div class="canvas">
  <section class="card card-front">
    <div class="glow"></div>
    <h1 class="brand-name">RWT FITTINGS LTD</h1>
    <div class="accent-bar"></div>
    <h2 class="person-name">MARCO PELTIERI</h2>
    <p class="person-role">Owner &amp; Manager</p>
    <address class="address">1407-5194 Linden Row<br>Burnaby BC, V5H 2K9</address>
    <ul class="contacts">
      <li>
        <svg viewBox="0 0 12 12" aria-hidden="true"><path d="M3 1 L5 3.5 L4 5 Q5 7.5 7 8 L8.5 7 L11 9 L9.5 11 Q3 10 1 2.5 Z" fill="var(--brand-blue)"/></svg>
        16045518293
      </li>
      <li>
        <svg viewBox="0 0 12 12" aria-hidden="true"><rect x="1" y="2.5" width="10" height="7" fill="none" stroke="var(--brand-blue)" stroke-width="1.2"/><path d="M1 2.5 L6 6.5 L11 2.5" fill="none" stroke="var(--brand-blue)" stroke-width="1.2"/></svg>
        RWTFittings@mailbox-demo.com
      </li>
      <li>
        <svg viewBox="0 0 12 12" aria-hidden="true"><circle cx="6" cy="6" r="5" fill="none" stroke="var(--brand-blue)" stroke-width="1.1"/><ellipse cx="6" cy="6" rx="2.2" ry="5" fill="none" stroke="var(--brand-blue)" stroke-width="1"/><path d="M1 6 H11 M2 3.5 H10 M2 8.5 H10" stroke="var(--brand-blue)" stroke-width="0.9"/></svg>
        www.rwtfittings-demo.com
      </li>
    </ul>
  </section>

  <section class="card card-back">
    <div class="back-mark"></div>
    <p class="back-name">RWT FITTINGS LTD</p>
  </section>
</div>
</body>
</html>
```